Corvex Hiring Partners Business Cards

Business cards with logo design for a new recruiting company called "Corvex Hiring Partners"

incorporate RED & BLUE colors

Final design should reflect strength - clean, elegant design

Company name superimposed upon graphic (Greek Columns)

Please see attached Photos!!!

Industry/Entity Type

Business

Font styles to use
Decorative

Colors
ec2027
0555a3
85cae6

Requirements
Must have
• Must look very similar to attached design!!!

Want Company name superimposed upon graphic (Greek Columns)

Tag line at bottom must be included:
"Connecting Ambitious Companies with Outstanding Talent"

```html
<!DOCTYPE html>
<html lang="en">
<head>
<meta charset="utf-8">
<title>Corvex Hiring Partners – Business Card</title>
<link href="https://fonts.googleapis.com/css2?family=Lato:wght@400;700&display=swap" rel="stylesheet">
<style>
  :root {
    --backdrop: #6b6b6b;
    --card: #ffffff;
    --brand-red: #ec2027;
    --brand-blue: #0555a3;
    --name-blue: #1d3f73;
    --ink: #111111;
    --rule: #1a1a1a;
  }
  * { margin: 0; padding: 0; box-sizing: border-box; }
  html, body {
    width: 1200px;
    height: 900px;
    overflow: hidden;
    background: var(--backdrop);
    font-family: "Lato", sans-serif;
  }
  .business-card {
    position: absolute;
    left: 75px;
    top: 150px;
    width: 1050px;
    height: 600px;
    background: var(--card);
    overflow: hidden;
  }
  .brand-lockup {
    position: absolute;
    left: 70px;
    top: 140px;
    width: 330px;
    display: flex;
    align-items: center;
    gap: 22px;
  }
  .brand-mark {
    flex: none;
    width: 56px;
    height: 56px;
    background: var(--brand-blue);
  }
  .brand-name {
    font-weight: 700;
    font-size: 40px;
    line-height: 1.15;
    color: var(--brand-blue);
  }
  .contact-block {
    position: absolute;
    left: 560px;
    top: 205px;
  }
  .contact-name {
    font-weight: 700;
    font-size: 46px;
    color: var(--name-blue);
    margin-bottom: 26px;
    letter-spacing: -0.3px;
  }
  .contact-line {
    font-size: 27px;
    color: var(--ink);
    line-height: 1.35;
  }
  .footer-band {
    position: absolute;
    left: 0;
    bottom: 0;
    width: 1050px;
    height: 170px;
  }
  .tagline {
    position: absolute;
    left: 0;
    bottom: 42px;
    width: 1050px;
    text-align: center;
    font-weight: 700;
    font-size: 29px;
    color: #ffffff;
    letter-spacing: 0.2px;
  }
</style>
</head>
<body>
  <div class="business-card">
    <div class="brand-lockup">
      <div class="brand-mark"></div>
      <div class="brand-name">Corvex<br>Hiring<br>Partners</div>
    </div>

    <div class="contact-block">
      <p class="contact-name">Daniel R Whitmore</p>
      <p class="contact-line">512 555 014</p>
      <p class="contact-line">CorvexHP.com</p>
      <p class="contact-line">DWhitmore@CorvexHP.com</p>
    </div>

    <svg class="footer-band" viewBox="0 0 1050 170" aria-hidden="true">
      <polygon points="0,52 1050,8 1050,14 0,58" fill="var(--rule)"/>
      <polygon points="0,68 1050,22 1050,170 0,170" fill="var(--brand-red)"/>
    </svg>
    <p class="tagline">Connecting Ambitious Companies with Outstanding Talent</p>
  </div>
</body>
</html>
```